New Website Announcement

We need a flyer to announce our new website to customers and prospective clients. The website will be launching soon, but I can provide a detailed outline in PDF form with copy and imagery to serve as inspiration for this design.

I would like a postcard size document that can be mailed in an envelope (no need for postcard style mailer info on 1 side)

About my company:

Verity Lane Studio is a new breed of marketing consulting agency built for the next frontier of consumer learning. Social interaction will be at the heart of great insights going forward – in how consumers engage with brands and in how organizations socialize what they learn to gain competitive advantage.
By fusing innovative insights techniques, technology and compelling graphic design-based reporting, we ensure results get noticed and make an impact.

contact info that can also be included:

Email: marek@veritylane-studio.net

Phone: 518-732-5164

Thanks

Attention all designers submitting a design for this project. Please keep in mind a few important details about this project.

1. Remember that the main objective of this postcard is to announce my new website.

2. Please be sure to read the brief for the copy I would like on each side. You can be creative in how it is displayed, but I need this key information somewhere. All other copy on the attached files is for your background only.

3. Please do not submit overly simple designs that just take the images I provided and overlay a text box with my copy. I could easily do this myself in PowerPoint in 5 minutes.

4. Remember that the design should be edgy and modern but needs to be professional and speak to a business audience.

Please submit any questions. Thank you for your submissions. 

Marek

Target Market(s)

senior level marketing and research clients at large companies and agencies

Industry/Entity Type

Marketing

Requirements
Must have
• Main message:

Need an engaging way to tell customers and prospective clients that we have a new website and that they should come visit us online to learn more about out services, check out case studies and read about our exciting partnerships.

COPY TO USE - UPDATED

Side 1:
(logo)
Introducing Verity Lane Studio

Let’s talk about taking research out of the dark ages.

Visit our newly launched website to learn how and get in touch.

www.veritylane-studio.net

Side 2
Logo
followed by tagline:
Consumer insights that get noticed.
A leading-edge marketing partnership that really works.

Additional text to use on Side 2:
How we can help...

Think of us as your go-to resource for identifying and incorporating the most innovative and exciting techniques into your research programs. We carefully curate and develop close partnerships with the best of the best - from online qualitative research and mobile ethnography to social media listening and fresh takes on concept testing, we can guide the way.

Plus, we believe that socializing consumer learning is just as critical as gathering it.By taking insights deliverables to the next level – through infographics, videos, magazines,interactive profiles and so much more – we are getting stakeholders excited to engage with research and inspired to take action because of it.
It’s a new way to look at insights from a new type of partner. And, it’s a new way to get the most from your research dollars.
Nice to have
• could incorporate our website main image of the lamp on white brick background which is attached, but not 100% mandatory.
Should not have
• - should not be too playful or young, but needs to be modern and design focused

- should not be cluttered or overly 'salesy'

- needs to be upscale and elegant / compelling and aligned with the look and feel of the website imagery (see attached)

```html
<!DOCTYPE html>
<html lang="en">
<head>
<meta charset="utf-8">
<title>Verity Lane Studio – New Website Postcard</title>
<link rel="stylesheet" href="https://fonts.googleapis.com/css2?family=PT+Sans:wght@400;700&family=PT+Sans+Narrow:wght@400;700&display=swap">
<style>
  :root {
    --brand-blue: #2f7cc4;
    --ink: #1d1d1d;
    --body-ink: #2a2a2a;
    --band-black: #111111;
    --page: #ffffff;
    --wall-light: #f4f4f3;
    --wall-mid: #d6d6d5;
    --wall-shade: #b9b9b8;
    --floor-light: #c4c4c2;
    --floor-dark: #8f8f8d;
    --card-shadow: rgba(0,0,0,0.28);
  }
  * { box-sizing: border-box; margin: 0; padding: 0; }
  html, body { width: 1200px; height: 449px; overflow: hidden; background: var(--page); }
  .canvas { position: relative; width: 1200px; height: 449px; }

  .card {
    position: absolute;
    top: 33px;
    height: 383px;
    overflow: hidden;
    box-shadow: 0 2px 8px var(--card-shadow);
    font-family: "PT Sans Narrow", "PT Sans", sans-serif;
    color: var(--ink);
  }

  /* Side 1 */
  .card-front { left: 33px; width: 565px; }
  .front-scene {
    position: absolute; inset: 0;
    background:
      radial-gradient(ellipse 190px 120px at 215px 115px, rgba(255,255,255,0.95) 0%, rgba(255,255,255,0) 100%),
      radial-gradient(ellipse 420px 260px at 280px 300px, rgba(255,255,255,0.35) 0%, rgba(255,255,255,0) 100%),
      linear-gradient(90deg, rgba(0,0,0,0.16) 0%, rgba(0,0,0,0) 18%, rgba(0,0,0,0) 82%, rgba(0,0,0,0.14) 100%),
      linear-gradient(180deg, var(--wall-light) 0%, #e7e7e6 35%, var(--wall-mid) 60%, var(--wall-shade) 68%, var(--floor-light) 70%, #b3b3b1 85%, var(--floor-dark) 100%);
  }
  .front-band { position: absolute; left: 0; right: 0; top: 143px; height: 5px; background: var(--band-black); }
  .front-url {
    position: absolute; left: 257px; top: 25px;
    font-family: "PT Sans", sans-serif; font-size: 18px; color: var(--brand-blue);
  }
  .front-copy {
    position: absolute; left: 323px; font-size: 14.5px; line-height: 17px; color: var(--ink);
  }
  .front-copy.first { top: 57px; }
  .front-copy.second { top: 96px; }
  .front-intro {
    position: absolute; left: 125px; top: 154px;
    font-family: "PT Sans", sans-serif; font-size: 13px; letter-spacing: 0.5px; color: var(--ink);
  }
  .front-brand {
    position: absolute; left: 122px; top: 171px;
    font-family: "PT Sans", sans-serif; font-weight: 700;
    font-size: 37px; line-height: 38px; color: var(--brand-blue);
  }
  .front-contact { position: absolute; left: 325px; top: 330px; font-family: "PT Sans", sans-serif; font-size: 10.5px; color: var(--ink); }
  .front-contact li { list-style: none; display: flex; align-items: center; gap: 5px; height: 15px; }
  .front-contact svg { width: 10px; height: 10px; }

  /* Side 2 */
  .card-back { left: 634px; width: 536px; background: var(--page); }
  .back-scene {
    position: absolute; left: 0; right: 0; top: 0; height: 122px;
    background:
      linear-gradient(90deg, rgba(0,0,0,0.08) 0%, rgba(0,0,0,0) 20%, rgba(0,0,0,0) 80%, rgba(0,0,0,0.08) 100%),
      linear-gradient(180deg, #ececeb 0%, #d8d8d7 45%, #c6c6c5 100%);
  }
  .back-band { position: absolute; left: 0; right: 0; top: 29px; height: 6px; background: var(--band-black); }
  .back-header-strip { position: absolute; left: 0; right: 0; top: 37px; height: 84px; background: rgba(255,255,255,0.55); }
  .back-brand {
    position: absolute; left: 38px; top: 47px;
    font-family: "PT Sans", sans-serif; font-weight: 700;
    font-size: 24px; line-height: 25px; color: var(--brand-blue);
  }
  .back-tagline { position: absolute; left: 187px; top: 64px; font-size: 15px; line-height: 22px; color: var(--ink); }
  .section-title {
    position: absolute; left: 37px;
    font-family: "PT Sans", sans-serif; font-weight: 700; font-size: 19px; color: var(--brand-blue);
  }
  .section-title.help { top: 136px; }
  .section-title.focus { top: 276px; }
  .help-copy {
    position: absolute; left: 37px; top: 162px; width: 492px;
    font-family: "PT Sans", sans-serif; font-size: 9.5px; line-height: 11.3px;
    color: var(--body-ink);
  }
  .focus-list { position: absolute; left: 0; right: 0; top: 308px; list-style: none; }
  .focus-item { position: absolute; top: 0; width: 160px; margin-left: -80px; text-align: center; font-size: 10.5px; color: var(--ink); }
  .focus-item svg { display: block; margin: 0 auto 8px; width: 26px; height: 26px; }
</style>
</head>
<body>
<main class="canvas">

  <section class="card card-front" aria-label="Postcard side one">
    <div class="front-scene" role="img" aria-label="Photograph of a curved floor lamp glowing in a white-painted brick room with a concrete floor"></div>
    <div class="front-band"></div>
    <p class="front-url">www.veritylane-studio.net</p>
    <p class="front-copy first">Let’s talk about taking research<br>out of the dark ages.</p>
    <p class="front-copy second">Visit our newly launched website<br>to learn how and get in touch.</p>
    <p class="front-intro">Introducing</p>
    <h1 class="front-brand">Verity Lane<br>Studio</h1>
    <ul class="front-contact">
      <li>
        <svg viewBox="0 0 10 10" aria-hidden="true"><rect x="0.5" y="2" width="9" height="6" fill="none" stroke="#1d1d1d" stroke-width="0.9"/><path d="M0.5 2 L5 5.5 L9.5 2" fill="none" stroke="#1d1d1d" stroke-width="0.9"/></svg>
        marek@veritylane-studio.net
      </li>
      <li>
        <svg viewBox="0 0 10 10" aria-hidden="true"><path d="M2 0.8 L3.6 2.8 L2.7 4 Q4 6.3 6 7.3 L7.2 6.4 L9.2 8 L8 9.4 Q3.8 9 0.7 2.1 Z" fill="#1d1d1d"/></svg>
        518-732-5164
      </li>
    </ul>
  </section>

  <section class="card card-back" aria-label="Postcard side two">
    <div class="back-scene" role="img" aria-label="Photograph of a white-painted brick wall"></div>
    <div class="back-band"></div>
    <div class="back-header-strip"></div>
    <h2 class="back-brand">Verity Lane<br>Studio</h2>
    <p class="back-tagline">Consumer insights that get noticed.<br>A leading-edge marketing partnership that really works</p>

    <h3 class="section-title help">How we can help…</h3>
    <div class="help-copy">
      <p>Think of us as your go-to resource for identifying and incorporating the most innovative and exciting techniques into your research programs. We carefully curate and develop close partnerships with the best of the best - from online qualitative research and mobile ethnography to social media listening and fresh takes on concept testing, we can guide the way.</p>
      <p>Plus, we believe that socializing consumer learning is just as critical as gathering it. By taking insights deliverables to the next level – through infographics, videos, magazines, interactive profiles and so much more – we are getting stakeholders excited to engage with research and inspired to take action because of it.</p>
      <p>It’s a new way to look at insights from a new type of partner. And, it’s a new way to get the most from your research dollars.</p>
    </div>

    <h3 class="section-title focus">We focus on designing the…</h3>
    <ul class="focus-list">
      <li class="focus-item" style="left:82px">
        <svg viewBox="0 0 26 26" aria-hidden="true"><circle cx="10" cy="10" r="7" fill="none" stroke="#1d1d1d" stroke-width="2.2"/><path d="M15 15 L23 23" stroke="#1d1d1d" stroke-width="3.4" stroke-linecap="round"/></svg>
        best research approach
      </li>
      <li class="focus-item" style="left:206px">
        <svg viewBox="0 0 26 26" aria-hidden="true"><path d="M1 9 L7 7 L13 10 L19 7 L25 9 L25 15 L20 16 L14 21 Q12 22 11 20 L6 16 L1 15 Z" fill="#1d1d1d"/><path d="M9 12 L14 16 M11 11 L16 15" stroke="#fff" stroke-width="1"/></svg>
        most flexible partnership
      </li>
      <li class="focus-item" style="left:317px">
        <svg viewBox="0 0 26 26" aria-hidden="true"><rect x="3" y="17" width="3" height="7" fill="#1d1d1d"/><rect x="8" y="14" width="3" height="10" fill="#1d1d1d"/><rect x="13" y="11" width="3" height="13" fill="#1d1d1d"/><rect x="18" y="7" width="3" height="17" fill="#1d1d1d"/><path d="M2 14 L8 9 L13 10 L22 3" fill="none" stroke="#1d1d1d" stroke-width="1.4"/><path d="M19 2 L23 2 L23 6" fill="none" stroke="#1d1d1d" stroke-width="1.4"/></svg>
        most impactful analysis
      </li>
      <li class="focus-item" style="left:432px">
        <svg viewBox="0 0 26 26" aria-hidden="true"><path d="M2 5 L10 5 L12 8 L24 8 L24 23 L2 23 Z" fill="#1d1d1d"/><path d="M13 20 L8.5 15.5 Q7 13 9.5 12 Q11.5 11.5 13 13.5 Q14.5 11.5 16.5 12 Q19 13 17.5 15.5 Z" fill="#fff"/></svg>
        most elegant, compelling deliverables
      </li>
    </ul>
  </section>

</main>
</body>
</html>
```